Business Card - MARLOW Real Estate

Design a professional business card for a real estate agent.

Target Market(s)

Residential property and home owners in the middle suburban eastern suburbs of Melbourne, Australia. Property prices range between $1m and $3m in value.

Industry/Entity Type

Real Estate

Contact Information for Business Card

FRONT: Black on White
MARLOW Real Estate logo
Felix Tarrant
Director / Officer in Effective Control / CEA PLKT
47 Quarry Lane,
Brindle Heights VIC 3987
Tel: 1800 562 907
Mob: 0488 216 740
E: felix@marlowrealestate-example.com.au
W. www.marlowrealestate-example.com.au

BACK: White on Black logo
MARLOW Real Estate logo
website: www.marlowrealestate-example.com.au

Colors
ffffff
000000

Requirements
Must have
• Detail as specified above
• White on black for front
• Black on white for back
Nice to have
• I may like to integrate my photo on the card;
• there will be other agents also requiring the card so a template would be useful
Should not have
• animations / drawings

```html
<!DOCTYPE html>
<html lang="en">
<head>
<meta charset="utf-8">
<title>MARLOW Real Estate – Business Card</title>
<link rel="stylesheet" href="https://fonts.googleapis.com/css2?family=Montserrat:wght@600;700&family=Questrial&display=swap">
<style>
  :root {
    --ink: #231f20;
    --paper: #ffffff;
    --backdrop: #6f7a8b;
    --photo-light: #e9e9ea;
    --photo-dark: #2b2c31;
  }
  * { margin: 0; padding: 0; box-sizing: border-box; }
  html, body { width: 1200px; height: 810px; overflow: hidden; }
  body {
    background: var(--backdrop);
    position: relative;
    font-family: "Questrial", "Century Gothic", sans-serif;
  }
  .card {
    position: absolute;
    width: 560px;
    height: 319px;
    top: 245px;
    overflow: hidden;
  }
  /* Back of card */
  .card--back { left: 20px; background: var(--ink); color: var(--paper); }
  .card--back .brand {
    position: absolute; left: 118px; top: 100px;
  }
  .card--back .brand__name {
    font-family: "Montserrat", sans-serif; font-weight: 600;
    font-size: 70px; line-height: 1; letter-spacing: 0.01em;
  }
  .card--back .brand__tag {
    font-family: "Montserrat", sans-serif; font-weight: 600;
    font-size: 13px; letter-spacing: 1.45em; margin-top: 10px;
  }
  .card--back .web {
    position: absolute; left: 118px; top: 278px;
    font-size: 12.5px; letter-spacing: 0.22em;
  }
  /* Front of card */
  .card--front { left: 620px; background: var(--paper); color: var(--ink); }
  .card--front .brand { position: absolute; left: 59px; top: 42px; }
  .card--front .brand__name {
    font-family: "Montserrat", sans-serif; font-weight: 600;
    font-size: 40px; line-height: 1; letter-spacing: 0.01em;
  }
  .card--front .brand__tag {
    font-family: "Montserrat", sans-serif; font-weight: 600;
    font-size: 7px; letter-spacing: 1.3em; margin-top: 3px;
  }
  .agent { position: absolute; left: 60px; top: 132px; }
  .agent__name {
    font-family: "Montserrat", sans-serif; font-weight: 700;
    font-size: 20px; line-height: 1.1;
  }
  .agent__role { font-size: 10.5px; margin-top: 2px; }
  .contact { position: absolute; left: 59px; list-style: none; }
  .contact__row { position: absolute; left: 0; display: flex; gap: 13px; white-space: nowrap; }
  .contact__row svg { width: 14px; height: 14px; margin-top: 1px; flex: none; }
  .contact__text { font-size: 12.3px; line-height: 15px; }
  .contact__row--address { top: 172px; }
  .contact__row--phone { top: 213px; }
  .contact__row--web { top: 248px; }
  .agent-photo {
    position: absolute; left: 355px; top: 25px; width: 165px; height: 264px;
    background: linear-gradient(180deg, var(--photo-light) 0%, var(--photo-dark) 35%, var(--photo-dark) 100%);
    border-radius: 40px 40px 0 0;
  }
  .base-band { position: absolute; left: 0; bottom: 0; width: 560px; height: 31px; }
</style>
</head>
<body>
  <section class="card card--back" aria-label="Card back">
    <div class="brand">
      <div class="brand__name">MARLOW</div>
      <div class="brand__tag">REAL ESTATE</div>
    </div>
    <div class="web">www.marlowrealestate-example.com.au</div>
  </section>

  <section class="card card--front" aria-label="Card front">
    <div class="brand">
      <div class="brand__name">MARLOW</div>
      <div class="brand__tag">REAL ESTATE</div>
    </div>

    <div class="agent">
      <div class="agent__name">Felix Tarrant</div>
      <div class="agent__role">Director/ / CEA PLKT</div>
    </div>

    <ul class="contact">
      <li class="contact__row contact__row--address">
        <svg viewBox="0 0 14 14" aria-hidden="true"><path d="M7 0.5a4.8 4.8 0 0 0-4.8 4.8C2.2 9 7 13.5 7 13.5s4.8-4.5 4.8-8.2A4.8 4.8 0 0 0 7 .5zm0 6.7a1.9 1.9 0 1 1 0-3.8 1.9 1.9 0 0 1 0 3.8z" fill="var(--ink)"/></svg>
        <span class="contact__text">47 Quarry Lane,<br>Brindle Heights VIC 3987</span>
      </li>
      <li class="contact__row contact__row--phone">
        <svg viewBox="0 0 14 14" aria-hidden="true"><path d="M3 1l2.2 2.6-1.2 1.6c.8 1.8 2.2 3.2 4 4l1.6-1.2L12.2 10l-1.3 2.4C6 12 2 8 1.6 3.1z" fill="var(--ink)"/></svg>
        <span class="contact__text">1800 562 907<br>0488 216 740</span>
      </li>
      <li class="contact__row contact__row--web">
        <svg viewBox="0 0 14 14" aria-hidden="true"><circle cx="7" cy="7" r="6.2" fill="var(--ink)"/><path d="M4 3.5c1.5.3 2 1.4 1.2 2.5-.7 1-.2 2 .8 2.3M9.5 2.8c-.7 1 .3 1.8 1.5 1.8M8.5 12.5c.2-1.5 1.5-2.3 2.8-2" stroke="var(--paper)" stroke-width="1.1" fill="none"/></svg>
        <span class="contact__text">felix@marlowrealestate-example.com.au<br>&nbsp;www.marlowrealestate-example.com.au</span>
      </li>
    </ul>

    <div class="agent-photo" role="img" aria-label="Portrait photo of the agent in a dark suit"></div>

    <svg class="base-band" viewBox="0 0 560 31" aria-hidden="true">
      <polygon points="298,31 330,0 560,0 560,31" fill="var(--ink)"/>
    </svg>
  </section>
</body>
</html>
```